Income Tax Flyer - Updates Needed

Just need to update this flyer design and give it a new look. We would like to keep all the same wording but make it stand out a little more. Our selling point is the "Same Day Tax Advance up to $6,000"

Lending, Small Loans, Tax Services, Title Loans, Personal Loans

```html
<!DOCTYPE html>
<html lang="en">
<head>
<meta charset="utf-8">
<title>Same Day Tax Advance Flyer</title>
<link rel="stylesheet" href="https://fonts.googleapis.com/css2?family=Roboto:wght@400;500;700;900&display=swap">
<style>
  :root {
    --green: #0f4a2c;
    --green-deep: #0b3d24;
    --red: #b5152b;
    --white: #ffffff;
    --ink: #1d1d1d;
    --card-shadow: 0 6px 18px rgba(0,0,0,0.12);
    --photo-light: #e9e9e6;
    --photo-mid: #bdbcb6;
    --photo-dark: #7d7d78;
  }
  * { margin: 0; padding: 0; box-sizing: border-box; }
  html, body { width: 927px; height: 1200px; overflow: hidden; background: var(--white); }
  body { font-family: 'Roboto', Arial, sans-serif; }
  .flyer { position: relative; width: 927px; height: 1200px; overflow: hidden; background: var(--white); }

  .hero-photo {
    position: absolute; left: 0; top: 0; width: 927px; height: 880px;
    background:
      radial-gradient(ellipse at 30% 25%, rgba(255,255,255,0.85), rgba(255,255,255,0) 60%),
      linear-gradient(160deg, var(--photo-light) 0%, #d6d5d0 45%, var(--photo-mid) 70%, var(--photo-dark) 100%);
  }
  .hero-veil { position: absolute; left: 0; top: 150px; width: 927px; height: 260px;
    background: linear-gradient(180deg, rgba(255,255,255,0) 0%, rgba(255,255,255,0.55) 40%, rgba(255,255,255,0) 100%); }

  .sweep { position: absolute; left: 0; top: 0; }

  .brand-corner {
    position: absolute; right: 0; top: 0; width: 322px; height: 146px;
    background: var(--white); border-bottom-left-radius: 146px;
    display: flex; align-items: center; justify-content: flex-end; padding-right: 28px; gap: 8px;
  }
  .brand-dot { width: 14px; height: 14px; border-radius: 50%; background: var(--red); }
  .brand-name { font-weight: 700; color: var(--green); font-size: 24px; line-height: 1.05; text-align: left; }

  .headline { position: absolute; left: 0; top: 188px; width: 927px; text-align: center; color: var(--green); font-weight: 700; }
  .headline-lead { font-size: 54px; letter-spacing: 1px; line-height: 70px; }
  .headline-amount { font-size: 58px; line-height: 76px; }
  .selling-point { margin-top: 6px; font-size: 30px; color: var(--red); font-weight: 500; }

  .mid-brand { position: absolute; left: 0; top: 562px; width: 927px; text-align: center;
    color: var(--green); font-weight: 700; font-size: 24px; }
  .offer-title { position: absolute; left: 0; top: 612px; width: 927px; text-align: center;
    color: var(--green); font-weight: 700; font-size: 33px; line-height: 42px; letter-spacing: 0.5px; }

  .features { position: absolute; top: 730px; left: 85px; display: flex; gap: 27px; }
  .feature-card { width: 235px; height: 209px; background: var(--white); box-shadow: var(--card-shadow);
    border-radius: 4px; display: flex; flex-direction: column; align-items: center; padding-top: 20px; }
  .feature-icon { width: 84px; height: 84px; border-radius: 50%; display: flex; align-items: center; justify-content: center; }
  .feature-icon.green { background: var(--green); }
  .feature-icon.red { background: var(--red); }
  .feature-label { margin-top: 24px; text-align: center; font-weight: 500; font-size: 19px; line-height: 30px; color: var(--ink); }

  .contact { position: absolute; top: 978px; left: 0; width: 927px; display: flex; justify-content: center; align-items: baseline; gap: 34px; }
  .contact-label { color: var(--green); font-weight: 700; font-size: 18px; }
  .contact-phone { color: var(--red); font-weight: 500; font-size: 30px; text-decoration: underline; text-underline-offset: 6px; text-decoration-thickness: 2px; }

  .locations { position: absolute; left: 0; top: 1080px; width: 927px; height: 120px; background: var(--green-deep); }
  .location { position: absolute; top: 0; width: 260px; text-align: center; color: var(--white); font-size: 19px; line-height: 32px; }
  .location-pin { position: absolute; top: -30px; left: 100px; width: 60px; height: 60px; border-radius: 50%;
    background: var(--red); border: 5px solid var(--white); display: flex; align-items: center; justify-content: center; }
  .location-text { padding-top: 48px; }
  .print-code { position: absolute; right: 18px; bottom: 14px; color: var(--white); font-size: 14px; }
</style>
</head>
<body>
<main class="flyer">
  <div class="hero-photo" role="img" aria-label="Photo of a hand using a calculator beside a laptop and a potted plant on a bright office desk"></div>
  <div class="hero-veil"></div>

  <svg class="sweep" width="927" height="1200" viewBox="0 0 927 1200" aria-hidden="true">
    <path d="M0 580 C 240 455, 560 430, 760 505 C 860 545, 910 580, 927 592 L927 1200 L0 1200 Z" fill="#b5152b"/>
    <path d="M0 592 C 250 470, 560 455, 750 545 C 855 600, 905 740, 927 860 L927 1200 L0 1200 Z" fill="#ffffff"/>
  </svg>

  <header class="brand-corner">
    <span class="brand-dot"></span>
    <span class="brand-name">Ledger One<br>Financial Group</span>
  </header>

  <section class="headline">
    <p class="headline-lead">APPLY HERE FOR</p>
    <p class="headline-amount">$5,000-$6,000 TODAY!</p>
    <p class="selling-point">Same Day Tax Advance up to $6,000</p>
  </section>

  <p class="mid-brand">Ledger One</p>
  <h2 class="offer-title">FILE YOUR TAXES AND<br>APPLY FOR AN EASY ADVANCE!</h2>

  <section class="features">
    <article class="feature-card">
      <div class="feature-icon green">
        <svg width="50" height="50" viewBox="0 0 50 50" fill="none" stroke="#fff" stroke-width="3" stroke-linecap="round">
          <path d="M40 16 A18 18 0 1 0 43 28"/>
          <path d="M40 8 L40 16 L32 16"/>
          <text x="25" y="30" fill="#fff" stroke="none" font-family="Roboto, Arial, sans-serif" font-size="13" font-weight="700" text-anchor="middle">24</text>
        </svg>
      </div>
      <p class="feature-label">AVAILABLE IN<br>24 HOURS OR LESS</p>
    </article>
    <article class="feature-card">
      <div class="feature-icon red">
        <svg width="50" height="50" viewBox="0 0 50 50" fill="none" stroke="#fff" stroke-width="3" stroke-linecap="round" stroke-linejoin="round">
          <circle cx="27" cy="15" r="9"/>
          <text x="27" y="20" fill="#fff" stroke="none" font-family="Roboto, Arial, sans-serif" font-size="13" font-weight="700" text-anchor="middle">$</text>
          <path d="M6 34 L14 34 L22 38 L30 38 M22 38 L38 34 L44 36 L30 44 L14 42 L6 42"/>
        </svg>
      </div>
      <p class="feature-label">CHOOSE YOUR<br>LOAN AMOUNT</p>
    </article>
    <article class="feature-card">
      <div class="feature-icon green">
        <svg width="50" height="50" viewBox="0 0 50 50" fill="none" stroke="#fff" stroke-width="3" stroke-linecap="round" stroke-linejoin="round">
          <circle cx="22" cy="22" r="15"/>
          <circle cx="22" cy="22" r="9"/>
          <text x="22" y="27" fill="#fff" stroke="none" font-family="Roboto, Arial, sans-serif" font-size="12" font-weight="700" text-anchor="middle">$</text>
          <path d="M32 31 L43 35 L38 37 L41 43 L38 44 L35 39 L32 42 Z" fill="#fff"/>
        </svg>
      </div>
      <p class="feature-label">QUICK AND<br>EASY</p>
    </article>
  </section>

  <section class="contact">
    <span class="contact-label">CONTACT US TODAY!</span>
    <span class="contact-phone">+1 (800) 555 0142</span>
  </section>

  <footer class="locations">
    <div class="location" style="left:62px">
      <span class="location-pin">
        <svg width="22" height="26" viewBox="0 0 22 26"><path d="M11 1 C5 1 1 5.5 1 11 C1 18 11 25 11 25 C11 25 21 18 21 11 C21 5.5 17 1 11 1 Z" fill="#fff"/><circle cx="11" cy="11" r="4" fill="#b5152b"/></svg>
      </span>
      <p class="location-text">465, Lorum Ipsum Doler,<br>United States</p>
    </div>
    <div class="location" style="left:334px">
      <span class="location-pin">
        <svg width="22" height="26" viewBox="0 0 22 26"><path d="M11 1 C5 1 1 5.5 1 11 C1 18 11 25 11 25 C11 25 21 18 21 11 C21 5.5 17 1 11 1 Z" fill="#fff"/><circle cx="11" cy="11" r="4" fill="#b5152b"/></svg>
      </span>
      <p class="location-text">465, Lorum Ipsum Doler,<br>Canada</p>
    </div>
    <div class="location" style="left:605px">
      <span class="location-pin">
        <svg width="22" height="26" viewBox="0 0 22 26"><path d="M11 1 C5 1 1 5.5 1 11 C1 18 11 25 11 25 C11 25 21 18 21 11 C21 5.5 17 1 11 1 Z" fill="#fff"/><circle cx="11" cy="11" r="4" fill="#b5152b"/></svg>
      </span>
      <p class="location-text">465, Lorum Ipsum Doler,<br>Australia</p>
    </div>
    <span class="print-code">C45</span>
  </footer>
</main>
</body>
</html>
```